Improved Business Card, Government Contracting

We are looking to update the design of our business cards. We would like to create a template that can be used for future employees and easy to update.

Halvorsen Advisory Partners, LLC is a Service Disabled Veteran Owned Small Business with headquarters located in Leavenworth, KS. Our current website is www.hvadpt.com. We have contracts in KS and VA with expansion opportunities in various other states. Our primary line of work is within government contracting and providing consulting services to various organizations within the Bureau of Civic Readiness. We would like to project a professional image of our company that is consistent with the industry. Provided are previous versions of our business card template that shows our logo as well. We would like to make sure the information on the cards are easily noticeable .

Target Market(s)

Government Officials
Fellow Small Business Contractors
Large Business Contractors (ex. TQLB, Pellwick Darrow, Fenwey Marsh Colquitt)

Industry/Entity Type

Business

Contact Information for Business Card

Dale Forsyth
Office Manager
Halvorsen Advisory Partners
Ph: 555.204.7716
Email: d.forsyth@hvadpt.us
www.hvadpt.com

Requirements
Must have
• The business mailing address is:
• 48730 212th Crescent
• Leavenworth, KS 66091
Nice to have
• Embossed lettering

```html
<!DOCTYPE html>
<html lang="en">
<head>
<meta charset="utf-8">
<title>Halvorsen Advisory Partners – Business Card</title>
<link rel="stylesheet" href="https://fonts.googleapis.com/css2?family=Lato:wght@400;700;900&display=swap">
<style>
  :root {
    --page-bg: #e9e7e3;
    --card-white: #ffffff;
    --card-grey: #e4e6ea;
    --strip-grey: #eef0f3;
    --brand-blue: #3b58b0;
    --brand-blue-light: #6a8ad2;
    --brand-blue-deep: #2c3f95;
    --accent-yellow: #f2ea2e;
    --ink: #1c1c22;
    --ink-blue: #4a5fb8;
    --white: #ffffff;
  }
  * { margin: 0; padding: 0; box-sizing: border-box; }
  html, body { width: 1200px; height: 1023px; overflow: hidden; }
  body {
    background: var(--page-bg);
    font-family: "Lato", sans-serif;
    position: relative;
  }
  .card {
    position: absolute;
    left: 232px;
    width: 736px;
    height: 420px;
    border-radius: 26px;
    overflow: hidden;
    box-shadow: 0 6px 18px rgba(0,0,0,0.18);
  }

  /* Front */
  .card-front {
    top: 48px;
    background: linear-gradient(180deg, var(--card-grey) 0%, var(--card-white) 45%);
  }
  .front-band { position: absolute; inset: 0; }
  .holder { position: absolute; left: 52px; top: 40px; }
  .holder-name {
    font-weight: 900; font-size: 34px; line-height: 1.2; color: var(--ink-blue); letter-spacing: 0.3px;
  }
  .holder-title { font-size: 24px; line-height: 1.25; color: var(--ink); }
  .address {
    position: absolute; left: 52px; top: 130px;
    font-style: normal; font-size: 24px; line-height: 1.28; color: var(--ink);
  }
  .address-company { color: var(--ink-blue); }
  .contacts { position: absolute; left: 52px; top: 296px; list-style: none; }
  .contacts li {
    display: flex; align-items: center; gap: 12px;
    font-size: 22px; color: var(--white); line-height: 1.45;
  }
  .contacts svg { width: 20px; height: 20px; flex: none; }
  .front-brand {
    position: absolute; right: 44px; top: 256px;
    display: flex; align-items: center; gap: 12px;
    color: var(--accent-yellow); font-weight: 700; font-size: 24px; line-height: 1.2;
  }
  .brand-square { width: 22px; height: 22px; background: var(--accent-yellow); flex: none; }

  /* Back */
  .card-back {
    top: 552px;
    background: linear-gradient(160deg, var(--brand-blue-light) 0%, var(--brand-blue) 45%, var(--brand-blue-deep) 100%);
  }
  .services { position: absolute; left: 54px; top: 54px; list-style: none; }
  .services li {
    display: flex; align-items: center; gap: 16px;
    font-size: 26px; color: var(--white); line-height: 1.6;
  }
  .tick-box { width: 26px; height: 26px; flex: none; }
  .back-brand {
    position: absolute; right: 48px; bottom: 52px;
    display: flex; align-items: center; gap: 12px;
    color: var(--accent-yellow); font-weight: 700; font-size: 26px;
  }
</style>
</head>
<body>

<section class="card card-front" aria-label="Business card front">
  <svg class="front-band" width="736" height="420" viewBox="0 0 736 420" aria-hidden="true">
    <defs>
      <linearGradient id="bandFill" x1="0" y1="0" x2="1" y2="1">
        <stop offset="0" stop-color="#6f8fd6"/>
        <stop offset="1" stop-color="#3b58b0"/>
      </linearGradient>
    </defs>
    <polygon points="0,282 736,222 736,404 0,404" fill="url(#bandFill)"/>
    <rect x="0" y="404" width="736" height="16" fill="var(--strip-grey)"/>
  </svg>

  <div class="holder">
    <p class="holder-name">Dale Forsyth</p>
    <p class="holder-title">Office Manager</p>
  </div>

  <address class="address">
    <span class="address-company">Halvorsen Advisory Partners</span><br>
    48730 212th Crescent<br>
    Leavenworth, KS 66091
  </address>

  <ul class="contacts">
    <li>
      <svg viewBox="0 0 20 20" aria-hidden="true"><rect x="1" y="3" width="18" height="14" rx="3" fill="#f2ea2e"/><path d="M6 7h8v6H6z" fill="#3b58b0"/></svg>
      555.204.7716
    </li>
    <li>
      <svg viewBox="0 0 20 20" aria-hidden="true"><rect x="1" y="4" width="18" height="12" fill="#f2ea2e"/><path d="M1 4l9 7 9-7" fill="none" stroke="#3b58b0" stroke-width="1.6"/></svg>
      d.forsyth@hvadpt.us
    </li>
    <li>
      <svg viewBox="0 0 20 20" aria-hidden="true"><circle cx="10" cy="10" r="8.5" fill="none" stroke="#f2ea2e" stroke-width="1.8"/><ellipse cx="10" cy="10" rx="3.6" ry="8.5" fill="none" stroke="#f2ea2e" stroke-width="1.4"/><path d="M1.5 10h17" stroke="#f2ea2e" stroke-width="1.4"/></svg>
      www.hvadpt.com
    </li>
  </ul>

  <div class="front-brand">
    <span class="brand-square" aria-hidden="true"></span>
    <span>Halvorsen Advisory Partners</span>
  </div>
</section>

<section class="card card-back" aria-label="Business card back">
  <ul class="services">
    <li><svg class="tick-box" viewBox="0 0 26 26" aria-hidden="true"><rect x="2" y="4" width="20" height="20" fill="none" stroke="#f2ea2e" stroke-width="2.4"/><path d="M7 13l5 6 11-16" fill="none" stroke="#f2ea2e" stroke-width="3"/></svg>Software &amp; Systems Engineering</li>
    <li><svg class="tick-box" viewBox="0 0 26 26" aria-hidden="true"><rect x="2" y="4" width="20" height="20" fill="none" stroke="#f2ea2e" stroke-width="2.4"/><path d="M7 13l5 6 11-16" fill="none" stroke="#f2ea2e" stroke-width="3"/></svg>Decision Analysis &amp; Process Improvement</li>
    <li><svg class="tick-box" viewBox="0 0 26 26" aria-hidden="true"><rect x="2" y="4" width="20" height="20" fill="none" stroke="#f2ea2e" stroke-width="2.4"/><path d="M7 13l5 6 11-16" fill="none" stroke="#f2ea2e" stroke-width="3"/></svg>Program &amp; Budget Analysis</li>
    <li><svg class="tick-box" viewBox="0 0 26 26" aria-hidden="true"><rect x="2" y="4" width="20" height="20" fill="none" stroke="#f2ea2e" stroke-width="2.4"/><path d="M7 13l5 6 11-16" fill="none" stroke="#f2ea2e" stroke-width="3"/></svg>Command and Control</li>
    <li><svg class="tick-box" viewBox="0 0 26 26" aria-hidden="true"><rect x="2" y="4" width="20" height="20" fill="none" stroke="#f2ea2e" stroke-width="2.4"/><path d="M7 13l5 6 11-16" fill="none" stroke="#f2ea2e" stroke-width="3"/></svg>Program Management</li>
  </ul>

  <div class="back-brand">
    <span class="brand-square" aria-hidden="true"></span>
    <span>Halvorsen Advisory Partners</span>
  </div>
</section>

</body>
</html>
```